The Linen Loft Co

We need a business card design for our wardrobe company.
Please visit our website www.gentlelinenlofts.com to get an idea of who we are.

```html
<!DOCTYPE html>
<html lang="en">
<head>
<meta charset="utf-8">
<title>The Linen Loft Co – Business Card</title>
<link href="https://fonts.googleapis.com/css2?family=Montserrat:wght@400;500&family=Open+Sans:wght@600&display=swap" rel="stylesheet">
<style>
  :root {
    --backdrop: #98d0c5;
    --card-dark: #151515;
    --card-mid: #232323;
    --frame-line: #8a8a8a;
    --brand-grey: #6a6a6a;
    --contact-text: #e2e2e2;
  }
  * { box-sizing: border-box; margin: 0; padding: 0; }
  html, body {
    width: 1200px;
    height: 800px;
    overflow: hidden;
    background: var(--backdrop);
  }
  .canvas {
    position: relative;
    width: 1200px;
    height: 800px;
  }
  .business-card {
    position: absolute;
    left: 180px;
    top: 160px;
    width: 840px;
    height: 480px;
    border-radius: 22px;
    overflow: hidden;
    background: var(--card-dark);
  }
  .wardrobe-photo {
    position: absolute;
    inset: 0;
    background: linear-gradient(100deg, #121212 0%, var(--card-mid) 45%, #1d1d1d 70%, #111 100%);
  }
  .inner-frame {
    position: absolute;
    left: 34px;
    top: 40px;
    right: 34px;
    bottom: 40px;
    border: 3px solid var(--frame-line);
    border-radius: 14px;
  }
  .brand {
    position: absolute;
    left: 272px;
    top: 98px;
    display: flex;
    align-items: center;
    gap: 22px;
  }
  .brand-mark {
    width: 44px;
    height: 44px;
    border: 3px solid var(--brand-grey);
  }
  .brand-name {
    font-family: "Montserrat", sans-serif;
    font-weight: 400;
    font-size: 30px;
    letter-spacing: 0.5px;
    text-transform: uppercase;
    color: var(--brand-grey);
  }
  .tagline {
    position: absolute;
    left: 376px;
    top: 156px;
    font-family: "Montserrat", sans-serif;
    font-weight: 500;
    font-size: 26px;
    color: var(--brand-grey);
  }
  .contact-list {
    position: absolute;
    left: 0;
    right: 0;
    top: 300px;
    list-style: none;
    font-family: "Open Sans", sans-serif;
    font-weight: 600;
    font-size: 19px;
    color: var(--contact-text);
    text-align: center;
    line-height: 30px;
  }
  .contact-item {
    display: flex;
    justify-content: center;
    align-items: center;
    gap: 10px;
  }
  .contact-icon {
    width: 14px;
    height: 14px;
    fill: var(--contact-text);
  }
</style>
</head>
<body>
<main class="canvas">
  <section class="business-card">
    <div class="wardrobe-photo" role="img" aria-label="Dark photograph of a walk-in wardrobe with hanging clothes and shelves"></div>
    <div class="inner-frame"></div>

    <div class="brand">
      <span class="brand-mark"></span>
      <span class="brand-name">The Linen Loft Co</span>
    </div>
    <p class="tagline">Made to Fit Every Room</p>

    <ul class="contact-list">
      <li class="contact-item">
        <svg class="contact-icon" viewBox="0 0 14 14" aria-hidden="true"><path d="M7 0a5 5 0 0 0-5 5c0 3.6 5 9 5 9s5-5.4 5-9a5 5 0 0 0-5-5zm0 7a2 2 0 1 1 0-4 2 2 0 0 1 0 4z"/></svg>
        <span>Fern Court, 42 Mill Lane, London N4 7QT</span>
      </li>
      <li class="contact-item">
        <svg class="contact-icon" viewBox="0 0 14 14" aria-hidden="true"><path d="M1 4c0-2 3-3 6-3s6 1 6 3v1.5h-3V4H4v1.5H1zM3 7l2-2h4l2 2v5H3zm4 1.2a1.6 1.6 0 1 0 0 3.2 1.6 1.6 0 0 0 0-3.2z"/></svg>
        <span>0207 555 0186</span>
      </li>
      <li class="contact-item">
        <svg class="contact-icon" viewBox="0 0 14 14" aria-hidden="true"><path d="M0 3h14v8H0zm1.2 1L7 8l5.8-4z" fill-rule="evenodd"/></svg>
        <span>info@gentlelinenlofts.com</span>
      </li>
      <li class="contact-item">
        <svg class="contact-icon" viewBox="0 0 14 14" aria-hidden="true"><path d="M7 0a7 7 0 1 0 0 14A7 7 0 0 0 7 0zm0 1.5c.8 0 1.7 2 1.8 4.7H5.2C5.3 3.5 6.2 1.5 7 1.5zM5.2 7.8h3.6C8.7 10.5 7.8 12.5 7 12.5s-1.7-2-1.8-4.7zM1.6 6.2a5.5 5.5 0 0 1 2.3-3.7 9 9 0 0 0-.9 3.7zm0 1.6H3a9 9 0 0 0 .9 3.7 5.5 5.5 0 0 1-2.3-3.7zm8.5 3.7a9 9 0 0 0 .9-3.7h1.4a5.5 5.5 0 0 1-2.3 3.7zM11 6.2a9 9 0 0 0-.9-3.7 5.5 5.5 0 0 1 2.3 3.7z"/></svg>
        <span>gentlelinenlofts.com</span>
      </li>
    </ul>
  </section>
</main>
</body>
</html>
```